Coastline Premier Retreats Business Card Design

Design a business card for Coastline Premier Retreats. Look at the website for colors and reference. Card should have logo, name, title, office number, mobile number, email, URL and a tagline like, "Luxury Hotel & Resort Email Marketing" (This might change).

https://www.coastlinepremierretreats.example

The rest I will leave up to your imagination.

Contact Information for Business Card

Logo, name, title, office number, mobile number, email, URL and a tagline like, "Luxury Hotel & Resort Email Marketing" (This might change).

```html
<!DOCTYPE html>
<html lang="en">
<head>
<meta charset="utf-8">
<title>Coastline Premier Retreats – Business Card</title>
<link href="https://fonts.googleapis.com/css2?family=Arimo:wght@400;700&display=swap" rel="stylesheet">
<style>
  :root {
    --bg: #b9b9bb;
    --paper: #ffffff;
    --orange: #f57c0c;
    --ink: #1c1c1c;
    --grey: #7d7d7d;
    --rule: #d6d6d6;
    --black-top: #2a2a2a;
    --black-bottom: #050505;
  }
  * { margin: 0; padding: 0; box-sizing: border-box; }
  html, body { width: 1200px; height: 876px; overflow: hidden; }
  body {
    background: var(--bg);
    font-family: "Arimo", Arial, sans-serif;
    position: relative;
  }
  .card {
    position: absolute;
    width: 520px;
    height: 297px;
    overflow: hidden;
    box-shadow: 0 10px 24px rgba(0,0,0,.25);
  }
  .card--front { left: 50px; top: 330px; background: var(--paper); }
  .card--back {
    left: 630px; top: 250px;
    background: linear-gradient(135deg, var(--black-top), var(--black-bottom) 70%);
  }
  .card__art { position: absolute; inset: 0; }
  .brand {
    position: absolute;
    font-weight: 700;
    text-transform: uppercase;
    line-height: 1;
    display: flex;
    align-items: center;
    gap: 8px;
  }
  .brand__mark { width: 11px; height: 11px; background: var(--orange); flex: none; }
  .brand__name { display: flex; flex-direction: column; }
  .brand__main { font-size: 28px; letter-spacing: .5px; }
  .brand__sub { font-size: 9.5px; letter-spacing: 2.6px; margin-top: 4px; }
  .card--front .brand { left: 24px; top: 142px; color: var(--ink); }
  .card--back .brand { left: 50%; top: 50%; transform: translate(-50%, -50%); gap: 10px; color: #fff; }
  .card--back .brand__mark { width: 12px; height: 12px; }
  .card--back .brand__main { font-size: 40px; letter-spacing: 1px; }
  .card--back .brand__sub { font-size: 13.5px; letter-spacing: 3.8px; }
  .contact {
    position: absolute;
    left: 232px;
    top: 112px;
    padding-left: 12px;
    border-left: 1px solid var(--rule);
    color: var(--grey);
    font-size: 12px;
    line-height: 1.4;
  }
  .contact__name {
    color: var(--orange);
    font-weight: 700;
    font-size: 15px;
    text-transform: uppercase;
    letter-spacing: .3px;
  }
  .contact__title { margin-bottom: 3px; }
  .contact__list { list-style: none; margin-top: 4px; }
  .contact__list li { display: flex; align-items: center; gap: 6px; }
  .contact__icon { width: 10px; height: 10px; flex: none; }
</style>
</head>
<body>

<section class="card card--front" aria-label="Business card front">
  <svg class="card__art" viewBox="0 0 520 297" aria-hidden="true">
    <path d="M0,0 H520 V108 C470,94 420,76 360,62 C280,44 230,10 130,8 C70,6 30,12 0,18 Z" fill="var(--orange)"/>
    <path d="M0,26 C60,14 150,14 220,34 C270,48 310,60 350,68 C300,62 260,54 215,46 C150,32 70,32 0,42 Z" fill="var(--ink)"/>
  </svg>

  <div class="brand">
    <span class="brand__mark"></span>
    <span class="brand__name">
      <span class="brand__main">Coastline</span>
      <span class="brand__sub">Premier Retreats</span>
    </span>
  </div>

  <div class="contact">
    <p class="contact__name">Daniel Hartley</p>
    <p class="contact__title">Manager</p>
    <p>Your Address, City<br>State, Zip 0000</p>
    <ul class="contact__list">
      <li>
        <svg class="contact__icon" viewBox="0 0 10 10"><path d="M2,0.5 L4,2.5 L3,4 C3.6,5.4 4.6,6.4 6,7 L7.5,6 L9.5,8 L8,9.5 C4,9 1,6 0.5,2 Z" fill="var(--orange)"/></svg>
        123-456-2100
      </li>
      <li>
        <svg class="contact__icon" viewBox="0 0 10 10"><rect x="2.5" y="0.5" width="5" height="9" rx="1" fill="none" stroke="var(--orange)"/></svg>
        123-456-2100
      </li>
      <li>
        <svg class="contact__icon" viewBox="0 0 10 10"><rect x="0.5" y="2" width="9" height="6" fill="none" stroke="var(--orange)"/><path d="M0.5,2 L5,5.5 L9.5,2" fill="none" stroke="var(--orange)"/></svg>
        youremail@mailbox.example
      </li>
      <li>
        <svg class="contact__icon" viewBox="0 0 10 10"><circle cx="5" cy="5" r="4.5" fill="var(--orange)"/><path d="M0.5,5 H9.5 M5,0.5 V9.5" stroke="#fff" stroke-width=".8"/></svg>
        www.yourwebsite.com
      </li>
    </ul>
  </div>
</section>

<section class="card card--back" aria-label="Business card back">
  <div class="brand">
    <span class="brand__mark"></span>
    <span class="brand__name">
      <span class="brand__main">Coastline</span>
      <span class="brand__sub">Premier Retreats</span>
    </span>
  </div>
</section>

</body>
</html>
```